Website homepage rework for women's travel website

I have a homepage (http://www.ladies-at-the-helm.com) that I'm 50% happy with but don't want to completely overhaul. I'd like to retain a similar look but upgrade it to something a bit more modern and less old-fashioned. The basic sense of the site is empowering, self-confident, fun and adventurous - but female and over 40.

A number of the elements on the page have to be redesigned, a few can be tweaked, and a few left alone. See the rest of the brief for further information.

Target Market(s)

women over 40 who like to travel

Industry/Entity Type

Travel

Number of Pages Required

1 page

Font styles to use
Other font styles liked:
• see my brief

Requirements
Must have
• - size - the page must be significantly wider
• - the only font I MUST keep is Raleway (as in the tagline) and possibly the font of the site name (Ladies at the Helm). Both of those work for me. There are too many fonts on the page, however, and that needs to be unified.
• - the rectangles I click to get inside the site have to change to something more modern, possibly square - they do not have to be separated into two columns as they are now, nor do they need the titles (toolkit etc)
• - I like the background image of the header - but it needs to be wider of course - also keep in mind the aspect - it has to fit into the smaller inside pages, whose size will not change
• - at the end of the project I need to receive the separate elements of the design so I can eventually make a change myself if needed ie. replace my own photo, for example
Nice to have
• - the three photos need to change to something more eye-popping - or something else should take their place to fill the space
Should not have
• I do not want a full, original redesign. I want my readers to still feel as though they are on the same site - same header, mostly same fonts.

```html
<!DOCTYPE html>
<html lang="en">
<head>
<meta charset="utf-8">
<title>Ladies at the Helm</title>
<link rel="stylesheet" href="https://fonts.googleapis.com/css2?family=Raleway:wght@400;500;600&display=swap">
<style>
:root{
  --ink:#2e2b2b;
  --band:#ebebeb;
  --accent:#e8641b;
  --text:#333;
  --muted:#666;
  --white:#fff;
  --rule:#dcdcdc;
  --red:#e0312b;
  --purple:#a0359a;
  --flame:#e8461b;
  --green:#3aa02c;
  --gold:#d4a80a;
  --teal:#2fd0b8;
  --crimson:#e02828;
  --sky:#3a9ed8;
  --footer:#e8e8e8;
}
*{margin:0;padding:0;box-sizing:border-box}
html,body{width:1200px;height:3010px;overflow:hidden;background:var(--white)}
body{font-family:'Raleway',sans-serif;color:var(--text);position:relative}
a{color:inherit;text-decoration:none}

.main-nav{height:68px;background:var(--ink);display:flex;justify-content:center;align-items:center}
.main-nav a{color:var(--white);font-weight:600;font-size:19px;padding:0 18px}

.hero{position:relative;height:438px;overflow:hidden;
  background:
    radial-gradient(ellipse 500px 220px at 80% 20%,rgba(255,240,120,.75),transparent 70%),
    radial-gradient(ellipse 420px 200px at 15% 10%,rgba(214,72,20,.55),transparent 70%),
    radial-gradient(ellipse 380px 160px at 60% 30%,rgba(230,110,30,.45),transparent 70%),
    linear-gradient(180deg,#e9901c 0%,#f2b226 40%,#f4c24a 52%,#d48a3a 62%,#b07a48 100%)}
.hero-mesas{position:absolute;left:0;right:0;top:210px;height:110px;
  background:
    radial-gradient(ellipse 160px 70px at 18% 60%,#8e2f14,transparent 75%),
    radial-gradient(ellipse 200px 90px at 78% 55%,#9c3618,transparent 75%),
    radial-gradient(ellipse 130px 60px at 96% 70%,#a23c1c,transparent 75%),
    linear-gradient(180deg,rgba(178,67,28,0) 0%,rgba(178,67,28,.5) 55%,rgba(122,46,24,.6) 100%)}
.hero-ground{position:absolute;left:0;right:0;top:300px;bottom:0;
  background:
    radial-gradient(ellipse 300px 60px at 70% 90%,rgba(80,80,90,.55),transparent 75%),
    linear-gradient(180deg,#b28a5a 0%,#8e7a58 40%,#6e6448 100%)}
.hero-portrait{position:absolute;left:158px;top:52px;width:324px;height:386px;border-radius:150px 150px 0 0;
  background:
    radial-gradient(ellipse 110px 70px at 48% 16%,#f1dfa2,transparent 80%),
    radial-gradient(ellipse 90px 110px at 48% 38%,#e8b89a,transparent 80%),
    radial-gradient(ellipse 60px 70px at 52% 80%,#e2453c,transparent 80%),
    linear-gradient(180deg,#e6cf98 0%,#dcb596 35%,#d4d4c2 58%,#bdbfae 100%)}
.site-name{position:absolute;left:540px;top:48px;width:470px;text-align:center;
  font-weight:500;font-size:48px;color:var(--white)}
.tagline{position:absolute;left:530px;top:110px;width:490px;text-align:center;font-size:25px;color:var(--ink)}
.snapshots{position:absolute;left:572px;top:212px;width:440px;height:190px}
.snap{position:absolute;width:142px;height:160px;background:var(--white);padding:8px 8px 22px;box-shadow:0 3px 8px rgba(0,0,0,.4)}
.snap span{display:block;width:100%;height:100%}
.snap-1{left:0;top:24px;transform:rotate(-4deg)}
.snap-1 span{background:radial-gradient(ellipse at 40% 60%,#c47a52,transparent 70%),linear-gradient(160deg,#e8e0d4,#9a4a2e 55%,#5a2e20)}
.snap-2{left:150px;top:16px;transform:rotate(3deg)}
.snap-2 span{background:radial-gradient(ellipse at 55% 50%,#b08462,transparent 65%),linear-gradient(160deg,#d8d0c2,#8a6a48 60%,#4a3a2a)}
.snap-3{left:296px;top:0;transform:rotate(-2deg)}
.snap-3 span{background:radial-gradient(ellipse 30px 90px at 55% 60%,#3fb0c8,transparent 80%),linear-gradient(180deg,#1e6ad0,#5aa8e8 60%,#c8d8e0)}

.intro{height:222px;background:var(--band);text-align:center;padding-top:30px}
.intro-greeting{font-size:24px;color:var(--ink);font-weight:500}
.intro-greeting em{font-style:normal;color:var(--accent)}
.pillars{display:flex;justify-content:center;margin-top:28px}
.pillar{width:290px;padding:0 20px}
.pillar + .pillar{border-left:1px solid #d0d0d0}
.pillar h3{color:var(--accent);font-weight:500;font-size:19px;margin-bottom:18px}
.pillar p{font-size:14px;color:var(--muted);line-height:22px}

.cta-band{height:70px;background:var(--ink);color:var(--white);display:flex;align-items:center;justify-content:center;font-size:22px;font-weight:500}
.cta-band a{color:var(--accent)}

.share-rail{position:absolute;left:0;top:372px;width:78px;background:var(--white);box-shadow:1px 1px 6px rgba(0,0,0,.25);text-align:center}
.share-item{height:60px;border-bottom:1px solid #e3e3e3;display:flex;flex-direction:column;align-items:center;justify-content:center;font-size:11px;color:var(--muted)}
.share-item:last-child{border-bottom:none}
.share-dot{width:24px;height:24px;border-radius:4px;margin-bottom:3px}
.share-total{height:50px;font-size:12px}

.toolbar{width:884px;margin:38px auto 0;display:flex;justify-content:space-between;align-items:center}
.social{display:flex;gap:4px}
.social span{width:38px;height:38px;display:block}
.search{display:flex}
.search-field{width:144px;height:40px;border:1px solid #ccc;font-size:11px;color:#999;display:flex;align-items:center;padding-left:10px}
.search-btn{width:40px;height:40px;background:var(--red);display:flex;align-items:center;justify-content:center}

.section-title{text-align:center;font-size:22px;font-weight:500;color:var(--ink)}
.toolkit-title{margin-top:46px}
.card-grid{width:884px;margin:32px auto 0;display:grid;grid-template-columns:428px 428px;gap:28px}
.card{height:428px;display:block}
.card-photo{height:332px}
.card-label{height:96px;padding:20px 28px 0;color:var(--white)}
.card-label h4{font-weight:500;font-size:23px;margin-bottom:6px}
.card-label p{font-size:14px}
.divider{width:884px;margin:46px auto 0;border:none;border-top:2px solid var(--rule)}
.dest-title{margin-top:40px}

.photo-tapas{background:
  radial-gradient(ellipse 120px 90px at 55% 38%,#d8401e,transparent 75%),
  radial-gradient(ellipse 90px 60px at 62% 22%,#2e7a2a,transparent 75%),
  radial-gradient(ellipse 160px 110px at 30% 70%,#f08a6a,transparent 75%),
  radial-gradient(ellipse 140px 90px at 70% 65%,#d89a5a,transparent 75%),
  linear-gradient(160deg,#4a2a1e 0%,#9a6a50 30%,#efe4da 65%,#f6f0ea 100%)}
.photo-packing{background:
  radial-gradient(ellipse 90px 50px at 20% 18%,#c8402e,transparent 75%),
  radial-gradient(ellipse 80px 60px at 68% 82%,#e85a50,transparent 75%),
  radial-gradient(ellipse 120px 80px at 55% 45%,#4aa08a,transparent 75%),
  radial-gradient(ellipse 140px 90px at 25% 60%,#6a3a3a,transparent 75%),
  linear-gradient(160deg,#2e2e36 0%,#3e4a78 50%,#2a3a6a 100%)}
.photo-cruise{background:
  radial-gradient(ellipse 200px 60px at 50% 62%,#28a0ff,transparent 75%),
  radial-gradient(ellipse 220px 40px at 45% 48%,#7ad0ff,transparent 75%),
  radial-gradient(ellipse 260px 90px at 50% 55%,#d8dce8,transparent 70%),
  linear-gradient(180deg,#04060c 0%,#0c1230 45%,#16244a 75%,#2a2a30 100%)}
.photo-gear{background:
  radial-gradient(ellipse 100px 70px at 28% 20%,#6a5a4a,transparent 75%),
  radial-gradient(ellipse 110px 70px at 75% 55%,#3a9a8a,transparent 75%),
  radial-gradient(ellipse 90px 60px at 25% 70%,#8a8a8a,transparent 75%),
  radial-gradient(ellipse 60px 40px at 60% 80%,#d85a3a,transparent 75%),
  linear-gradient(160deg,#5a5248 0%,#d8d4cc 45%,#bdb8b0 75%,#7a746c 100%)}
.photo-lake{background:
  radial-gradient(ellipse 90px 200px at 8% 60%,#1e3a1e,transparent 75%),
  radial-gradient(ellipse 260px 80px at 70% 60%,#1a56a8,transparent 75%),
  radial-gradient(ellipse 220px 70px at 55% 28%,#6a7a6a,transparent 75%),
  linear-gradient(180deg,#9cc8ee 0%,#8aa4b0 22%,#4a6a72 40%,#1e5aa8 62%,#234a28 100%)}
.photo-risotto{background:
  radial-gradient(ellipse 160px 110px at 52% 58%,#f4a810,transparent 72%),
  radial-gradient(ellipse 40px 30px at 52% 40%,#3a7a2a,transparent 75%),
  radial-gradient(ellipse 240px 170px at 50% 55%,#f6f4ee,transparent 80%),
  linear-gradient(160deg,#8a8a70 0%,#d8d8c8 40%,#6a6a60 100%)}
.photo-gateway{background:
  radial-gradient(ellipse 110px 140px at 50% 60%,#4a3a6a,transparent 70%),
  radial-gradient(ellipse 40px 40px at 20% 30%,#2a8a6a,transparent 75%),
  radial-gradient(ellipse 180px 170px at 50% 62%,#c09060,transparent 75%),
  linear-gradient(180deg,#2c6ad8 0%,#5a8ad8 25%,#b08a5a 50%,#7a5a3a 100%)}
.photo-carouge{background:
  radial-gradient(ellipse 90px 60px at 40% 85%,#d83a3a,transparent 75%),
  radial-gradient(ellipse 140px 70px at 30% 78%,#3a7a2a,transparent 75%),
  radial-gradient(ellipse 70px 150px at 28% 40%,#c8c4b8,transparent 75%),
  radial-gradient(ellipse 110px 120px at 80% 55%,#e8dcc8,transparent 75%),
  linear-gradient(180deg,#2e86e0 0%,#6ab0ea 35%,#5a7a4a 70%,#2a4a22 100%)}

.footer{position:absolute;left:0;right:0;bottom:0;height:66px;background:var(--footer);display:flex;align-items:center;justify-content:center;font-size:14px;color:var(--muted)}
</style>
</head>
<body>

<nav class="main-nav">
  <a href="#">START HERE</a><a href="#">ABOUT</a><a href="#">TRAVEL RESOURCES</a><a href="#">BLOG</a><a href="#">TRAVEL SHOP</a><a href="#">CONTACT</a>
</nav>

<header class="hero" role="img" aria-label="Desert landscape with red mesas under a golden sky over a faded map">
  <div class="hero-mesas"></div>
  <div class="hero-ground"></div>
  <div class="hero-portrait" role="img" aria-label="Portrait of the site founder smiling, sunglasses on her head"></div>
  <div class="site-name">Ladies at the Helm</div>
  <p class="tagline">For women who travel smart, safe + solo</p>
  <div class="snapshots">
    <div class="snap snap-1"><span role="img" aria-label="Photo of an ornate wooden balcony"></span></div>
    <div class="snap snap-2"><span role="img" aria-label="Photo of a camel close up"></span></div>
    <div class="snap snap-3"><span role="img" aria-label="Photo of a tiled blue minaret"></span></div>
  </div>
</header>

<section class="intro">
  <p class="intro-greeting">Hi, I'm <em>Marlene</em>. I took my first solo trip at 15. I'll show you how to travel...</p>
  <div class="pillars">
    <div class="pillar"><h3>Smart</h3><p>Practical tools to help you plan – and<br>afford – the perfect trip</p></div>
    <div class="pillar"><h3>Safe</h3><p>Down-to-earth advice and a ton of<br>safety recommendations</p></div>
    <div class="pillar"><h3>Solo</h3><p>Yes, you can do it!</p></div>
  </div>
</section>

<div class="cta-band"><p>Thinking of solo travel? <a href="#">Click here</a> to find out how.</p></div>

<aside class="share-rail">
  <div class="share-item share-total">1.7k<br>Shares</div>
  <div class="share-item"><span class="share-dot" style="background:#3b5998"></span>1.5k</div>
  <div class="share-item"><span class="share-dot" style="background:#cb2027"></span>106</div>
  <div class="share-item"><span class="share-dot" style="background:#45b0e3"></span></div>
  <div class="share-item"><span class="share-dot" style="background:#e8384f"></span></div>
  <div class="share-item">
    <svg width="26" height="20" viewBox="0 0 26 20"><rect x="1" y="1" width="24" height="18" fill="none" stroke="#333" stroke-width="2"/><path d="M1 1 L13 11 L25 1" fill="none" stroke="#333" stroke-width="2"/></svg>
  </div>
  <div class="share-item"><span class="share-dot" style="background:#1a6fb5"></span></div>
</aside>

<main>
  <div class="toolbar">
    <div class="social">
      <span style="background:#3b5998"></span>
      <span style="background:#45b0e3"></span>
      <span style="background:#dd4b39"></span>
      <span style="background:#3f729b"></span>
      <span style="background:#cb2027"></span>
    </div>
    <div class="search">
      <div class="search-field">Search this site</div>
      <div class="search-btn">
        <svg width="16" height="16" viewBox="0 0 16 16"><circle cx="6.5" cy="6.5" r="4.5" fill="none" stroke="#fff" stroke-width="2"/><path d="M10 10 L14 14" stroke="#fff" stroke-width="2.4"/></svg>
      </div>
    </div>
  </div>

  <h2 class="section-title toolkit-title">Travel Toolkit</h2>
  <div class="card-grid">
    <a class="card" href="#"><div class="card-photo photo-tapas" role="img" aria-label="Plate of tapas with salmon and bread"></div><div class="card-label" style="background:var(--red)"><h4>Eating With Locals</h4><p>The ultimate guide to social dining</p></div></a>
    <a class="card" href="#"><div class="card-photo photo-packing" role="img" aria-label="Travel gear laid out on a blue blanket"></div><div class="card-label" style="background:var(--purple)"><h4>Your Packing List</h4><p>Take what you need - no more</p></div></a>
    <a class="card" href="#"><div class="card-photo photo-cruise" role="img" aria-label="Cruise ship lit up in blue at night"></div><div class="card-label" style="background:var(--flame)"><h4>No Singal Supplement</h4><p>17 ways to avoid paying it</p></div></a>
    <a class="card" href="#"><div class="card-photo photo-gear" role="img" aria-label="Clothes and toiletries spread on a bed"></div><div class="card-label" style="background:var(--green)"><h4>Stress Management Course</h4><p>How to travel stress - free</p></div></a>
  </div>

  <hr class="divider">

  <h2 class="section-title dest-title">Destinations</h2>
  <div class="card-grid">
    <a class="card" href="#"><div class="card-photo photo-lake" role="img" aria-label="Mountain lake framed by pine trees"></div><div class="card-label" style="background:var(--gold)"><h4>Solo In Argentina</h4><p>Does it really take two to tango?</p></div></a>
    <a class="card" href="#"><div class="card-photo photo-risotto" role="img" aria-label="Plate of saffron risotto"></div><div class="card-label" style="background:var(--teal)"><h4>Europe For Foodies</h4><p>9 top destinations to try in October</p></div></a>
    <a class="card" href="#"><div class="card-photo photo-gateway" role="img" aria-label="Tiled madrasa gateway under blue sky"></div><div class="card-label" style="background:var(--crimson)"><h4>Solo Female Travel</h4><p>A 3-week Central Asia itinerary</p></div></a>
    <a class="card" href="#"><div class="card-photo photo-carouge" role="img" aria-label="Stone monument with flowers before a town house"></div><div class="card-label" style="background:var(--sky)"><h4>Rebellious Carouge</h4><p>Geneva's Alter Ego?</p></div></a>
  </div>
</main>

<footer class="footer">Copyright © 2016 Ladies at the Helm. All Rights Reserved</footer>

</body>
</html>
```